Pellmora Business Cards

Create new business cards with the details below.

Stuart Kovan
Director

MB: +61 427 315 964
PH: 1300 647 519
Email: stuart.kovan@pellmora.com.au
Address: 27D Halden Parade, Brookvale VIC 3174 Australia
Website: www.pellmora.com.au

Target Market(s)

Other business

Industry/Entity Type

Business

Requirements
Must have
• must be clean looking

```html
<!DOCTYPE html>
<html lang="en">
<head>
<meta charset="utf-8">
<title>Pellmora Business Cards</title>
<link rel="stylesheet" href="https://fonts.googleapis.com/css2?family=Montserrat:wght@700&family=Roboto+Condensed:wght@400;700&display=swap">
<style>
  :root {
    --backdrop: #e9e8e4;
    --card: #ffffff;
    --green: #86c232;
    --ink: #1e1e1e;
    --muted: #3a3a3a;
  }
  html, body {
    margin: 0;
    width: 1200px;
    height: 913px;
    overflow: hidden;
    background: var(--backdrop);
  }
  .canvas {
    position: relative;
    width: 1200px;
    height: 913px;
  }
  .card {
    position: absolute;
    width: 520px;
    height: 317px;
    background: var(--card);
    box-shadow: 0 6px 18px rgba(0,0,0,0.18);
    overflow: hidden;
  }
  .card::before {
    content: "";
    position: absolute;
    left: 0; top: 0; bottom: 0;
    width: 12px;
    background: var(--green);
  }
  .card-front { left: 60px; top: 120px; }
  .card-back { left: 620px; top: 476px; }

  .brand {
    position: absolute;
    display: flex;
    align-items: center;
    gap: 14px;
  }
  .brand-mark {
    width: 34px;
    height: 34px;
    background: var(--ink);
  }
  .brand-name {
    font-family: "Montserrat", sans-serif;
    font-weight: 700;
    color: var(--ink);
    letter-spacing: 1px;
    text-transform: uppercase;
    line-height: 1;
  }
  .card-front .brand { left: 70px; top: 136px; }
  .card-front .brand-name { font-size: 46px; }
  .card-front .brand-mark { width: 44px; height: 44px; }

  .card-back .brand { right: 34px; top: 30px; gap: 10px; }
  .card-back .brand-name { font-size: 26px; }
  .card-back .brand-mark { width: 24px; height: 24px; }

  .person {
    position: absolute;
    left: 42px;
    top: 118px;
  }
  .person-name {
    font-family: "Montserrat", sans-serif;
    font-weight: 700;
    font-size: 19px;
    color: var(--ink);
    margin: 0;
  }
  .person-role {
    font-family: "Roboto Condensed", sans-serif;
    font-size: 14px;
    color: var(--muted);
    margin: 6px 0 0;
  }
  .contact-list {
    position: absolute;
    left: 42px;
    bottom: 26px;
    margin: 0;
    padding: 0;
    list-style: none;
    font-family: "Roboto Condensed", sans-serif;
    font-size: 14px;
    color: var(--ink);
  }
  .contact-list li {
    display: flex;
    align-items: center;
    gap: 10px;
    height: 21px;
  }
  .contact-list li.strong { font-weight: 700; }
  .contact-icon { width: 14px; height: 14px; flex: none; }
  .contact-icon * { fill: var(--green); }
</style>
</head>
<body>
<main class="canvas">

  <section class="card card-front" aria-label="Business card front">
    <div class="brand">
      <span class="brand-mark"></span>
      <span class="brand-name">Pellmora</span>
    </div>
  </section>

  <section class="card card-back" aria-label="Business card back">
    <div class="brand">
      <span class="brand-mark"></span>
      <span class="brand-name">Pellmora</span>
    </div>

    <div class="person">
      <p class="person-name">Stuart Kovan</p>
      <p class="person-role">Director</p>
    </div>

    <ul class="contact-list">
      <li>
        <svg class="contact-icon" viewBox="0 0 14 14" aria-hidden="true"><path d="M7 0a5 5 0 0 0-5 5c0 3.5 5 9 5 9s5-5.5 5-9a5 5 0 0 0-5-5zm0 7a2 2 0 1 1 0-4 2 2 0 0 1 0 4z"/></svg>
        27D Halden Parade, Brookvale VIC 3174 Australia
      </li>
      <li>
        <svg class="contact-icon" viewBox="0 0 14 14" aria-hidden="true"><path d="M3.5 0h7a1 1 0 0 1 1 1v12a1 1 0 0 1-1 1h-7a1 1 0 0 1-1-1V1a1 1 0 0 1 1-1zm1 2v8h5V2zm2.5 9.2a.8.8 0 1 0 0 1.6.8.8 0 0 0 0-1.6z"/></svg>
        +61 427 315 964
      </li>
      <li>
        <svg class="contact-icon" viewBox="0 0 14 14" aria-hidden="true"><path d="M1 4c0-2 2-3 6-3s6 1 6 3v1.5h-3V4H4v1.5H1zm2.5 3h7l1.5 6H2zm3.5 1.3a1.7 1.7 0 1 0 0 3.4 1.7 1.7 0 0 0 0-3.4z"/></svg>
        1300 647 519
      </li>
      <li class="strong">
        <svg class="contact-icon" viewBox="0 0 14 14" aria-hidden="true"><path d="M0 2.5h14v9H0zm1.2 1.2v.4L7 8l5.8-3.9v-.4z"/></svg>
        stuart.kovan@pellmora.com.au
      </li>
      <li class="strong">
        <svg class="contact-icon" viewBox="0 0 14 14" aria-hidden="true"><path d="M7 0a7 7 0 1 0 0 14A7 7 0 0 0 7 0zm4.9 6.3H9.8a10 10 0 0 0-.9-4 5.6 5.6 0 0 1 3 4zM7 1.5c.8 1 1.3 2.8 1.4 4.8H5.6C5.7 4.3 6.2 2.5 7 1.5zM5.1 2.3a10 10 0 0 0-.9 4H2.1a5.6 5.6 0 0 1 3-4zm-3 5.4h2.1a10 10 0 0 0 .9 4 5.6 5.6 0 0 1-3-4zM7 12.5c-.8-1-1.3-2.8-1.4-4.8h2.8c-.1 2-.6 3.8-1.4 4.8zm1.9-.8a10 10 0 0 0 .9-4h2.1a5.6 5.6 0 0 1-3 4z"/></svg>
        www.pellmora.com.au
      </li>
    </ul>
  </section>

</main>
</body>
</html>
```